4th Generation Family Business Needs a New Card Design!

We are a family owned 4th Generation company. We are based in the Sydney, Australia area and we are desperately in need of a more modern and classy card. We are monumental masons who design, supply & erect lasting memorials throughout cemeteries in Sydney. Our customers are normally in a period of grieving. I have attached logo files that will need to be implemented on the card. Company was established 1935. Australian Owned and Operated. Card needs to be designed to PIXO.com specification.

Target Market(s)

Our target market is based upon people that a grieving for family members that have passed away. We also deal with alot of companies that own and operate cemeteries.

Industry/Entity Type

Business

Contact Information for Business Card

Simon Harcourt, Operations Manager, 0417293086, simon@harcourtmemorials.com.au
Lewis Brannock, Director, 0491630572, lewis@harcourtmemorials.com.au
Phone # 02 9561 3048
Website: www.harcourtmemorials.com.au
Address: Suite 17, 8 Palfrey Lane, West Carlow, Sydney NSW 2156

Font styles to use
Serif
Decorative
Script

Requirements
Must have
• Would like to see the logo nicely implemented with a modern design. Embossed lettering would be a nice additive.

```html
<!DOCTYPE html>
<html lang="en">
<head>
<meta charset="utf-8">
<title>Harcourt Memorials – Business Card</title>
<link href="https://fonts.googleapis.com/css2?family=Montserrat:wght@400;500;600;700&display=swap" rel="stylesheet">
<style>
  :root {
    --backdrop: #2b2b2d;
    --gold: #ecbf2c;
    --gold-text: #e6b623;
    --ink: #111111;
    --paper: #ffffff;
    --muted: #2a2a2a;
  }
  * { box-sizing: border-box; margin: 0; padding: 0; }
  html, body {
    width: 1200px; height: 900px; overflow: hidden;
    background: var(--backdrop);
    font-family: "Montserrat", Arial, sans-serif;
  }
  .canvas { position: relative; width: 1200px; height: 900px; }
  .card {
    position: absolute; left: 240px;
    width: 720px; height: 410px;
    border-radius: 24px;
    box-shadow: 0 18px 40px rgba(0,0,0,.45);
  }
  .card--front { top: 30px; background: var(--gold); }
  .card--back  { top: 465px; background: var(--paper); }

  /* Front */
  .front-brand {
    position: absolute; left: 0; right: 0; top: 140px;
    display: flex; align-items: center; justify-content: center; gap: 18px;
  }
  .brand-square { width: 34px; height: 34px; background: var(--ink); }
  .brand-name {
    font-weight: 700; font-size: 44px; color: var(--ink);
    letter-spacing: 1px; text-transform: uppercase; line-height: 1.1;
  }
  .front-web {
    position: absolute; left: 0; right: 0; bottom: 46px;
    text-align: center; color: var(--paper);
    font-size: 17px; font-weight: 500; letter-spacing: .3px;
  }
  .front-web strong { font-weight: 700; }

  /* Back */
  .back-brand {
    position: absolute; left: 44px; top: 150px; width: 300px;
    display: flex; align-items: center; gap: 14px;
  }
  .back-brand .brand-square { width: 26px; height: 26px; flex: none; }
  .back-brand .brand-name { font-size: 30px; }

  .contact {
    position: absolute; left: 400px; top: 110px; width: 300px;
    color: var(--muted);
  }
  .contact__name {
    color: var(--gold-text); font-weight: 600; font-size: 27px; line-height: 1.1;
  }
  .contact__role { font-size: 15px; margin: 4px 0 12px; }
  .contact__address { font-size: 14px; line-height: 1.35; margin-bottom: 10px; }
  .contact__list { list-style: none; font-size: 14px; }
  .contact__list li {
    display: flex; align-items: center; gap: 8px; line-height: 1.55;
    white-space: nowrap;
  }
  .contact__list svg { width: 12px; height: 12px; flex: none; fill: var(--gold-text); }
  .contact__list strong { color: var(--gold-text); font-weight: 600; }
</style>
</head>
<body>
<main class="canvas">

  <section class="card card--front" aria-label="Card front">
    <div class="front-brand">
      <span class="brand-square" aria-hidden="true"></span>
      <span class="brand-name">Harcourt Memorials</span>
    </div>
    <p class="front-web">www.<strong>harcourtmemorials</strong>.com.au</p>
  </section>

  <section class="card card--back" aria-label="Card back">
    <div class="back-brand">
      <span class="brand-square" aria-hidden="true"></span>
      <span class="brand-name">Harcourt Memorials</span>
    </div>

    <div class="contact">
      <h1 class="contact__name">Lewis Brannock</h1>
      <p class="contact__role">Director</p>
      <p class="contact__address">Suite 17, 8 Palfrey Lane,<br>West Carlow, Sydney NSW 2156</p>
      <ul class="contact__list">
        <li>
          <svg viewBox="0 0 12 12" aria-hidden="true"><rect x="3" y="0.5" width="6" height="11" rx="1.2"/><rect x="4" y="1.8" width="4" height="7" fill="#fff"/></svg>
          <span>0491630572</span>
        </li>
        <li>
          <svg viewBox="0 0 12 12" aria-hidden="true"><path d="M2.4 1l2 2.2-1 1.4a7 7 0 0 0 4 4l1.4-1 2.2 2-1.3 1.9C5.4 11.3.7 6.6 .5 2.3z"/></svg>
          <span>02 9561 3048</span>
        </li>
        <li>
          <svg viewBox="0 0 12 12" aria-hidden="true"><rect x="0.5" y="2" width="11" height="8" rx="1"/><path d="M1 2.6l5 3.6 5-3.6" stroke="#fff" stroke-width="1" fill="none"/></svg>
          <span>lewis@harcourtmemorials.com.au</span>
        </li>
        <li>
          <svg viewBox="0 0 12 12" aria-hidden="true"><circle cx="6" cy="6" r="5.5"/><path d="M.6 6h10.8M6 .6c-3 3-3 7.8 0 10.8M6 .6c3 3 3 7.8 0 10.8" stroke="#fff" stroke-width=".8" fill="none"/></svg>
          <span>www.<strong>harcourtmemorials</strong>.com.au</span>
        </li>
      </ul>
    </div>
  </section>

</main>
</body>
</html>
```